Website design for Puddle Jump Kidscare

I need a website designed for my daycare business, Puddle Jump Kidscare, now that I have a new logo. My former website was ok but simple and I did not have a logo yet. It also was created by me using a template and was entirely pink. I loved the bright, happy feel of it but worried it might not appeal as much to potential clients who have sons. Therefore, I need a site which will appeal to both genders while still keeping the cheerful color scheme of my new logo, which has pinks, blue, green and cream.
Updates

Reason: Hello! I am still trying to download my new logo and am sorry it is taking me so long. Hopefully I will it posted by the end of today (US Eastern Standard Time). Thank you all very much for your patience!

Hello! I have finally managed to upload my new logo for you to use in designing my website. I'm sorry it took so long and greatly appreciate your time and creative efforts! I look forward to seeing what is submitted based on my logo design and its style/colors.

Many thanks!

Reason: As I've been traveling and posted my logo file late, I am extending my deadline. I am now back and can focus on providing more and better feedback. I appreciate your patience and submissions very much!

Reason: I need more time to provide feedback and make decisions.

Industry/Entity Type

Daycare

Colors
0192cd
33a6d7
86cae7
cadf82
fbf289
add136
e34197

```html
<!DOCTYPE html>
<html lang="en">
<head>
<meta charset="utf-8">
<title>Puddle Jump Kidscare</title>
<link href="https://fonts.googleapis.com/css2?family=Source+Sans+3:wght@400;600;700&family=Sniglet:wght@800&display=swap" rel="stylesheet">
<style>
:root{
  --blue:#2fa3d9;
  --blue-deep:#0192cd;
  --sky:#86cae7;
  --lime:#b9d65f;
  --green:#add136;
  --pink:#f2a0cb;
  --pink-deep:#e34197;
  --text:#7b8a95;
  --cream:#f7f7f2;
  --white:#ffffff;
}
*{margin:0;padding:0;box-sizing:border-box}
html,body{width:1024px;height:1200px;overflow:hidden;background:var(--white)}
body{position:relative;font-family:"Source Sans 3",sans-serif;color:var(--text)}
.abs{position:absolute}
.brand{font-family:"Source Sans 3",sans-serif;font-weight:700;color:var(--blue);line-height:1}
.header-brand{left:136px;top:20px;font-size:30px}
.contact-bar{top:28px;left:440px;display:flex;font-size:11px;color:var(--text)}
.contact-bar .item{display:flex;align-items:center;gap:8px;padding:0 20px;height:24px;border-left:1px solid #e3e3e3}
.contact-bar .item:last-child{padding-right:0}
.hero{left:0;top:99px;width:1024px;height:449px;background:linear-gradient(90deg,#e9c7a8 0%,#f1c4c4 25%,#f6e0d8 50%,#fbf4f2 70%,#fdfbfb 100%)}
.nav{left:134px;top:77px;width:753px;height:39px;background:var(--pink);border:1px solid #e98cbd;border-radius:2px;display:flex;padding-left:15px;box-shadow:0 2px 0 rgba(227,65,151,.25)}
.nav a{color:var(--white);text-decoration:none;font-weight:600;font-size:13px;line-height:39px;padding:0 17px}
.nav a.active{background:var(--blue);padding:0 23px}
.welcome{left:645px;top:244px}
.script{font-family:"Sniglet",sans-serif;font-weight:800;font-style:italic}
.welcome h1{font-size:26px;line-height:31px;color:var(--blue)}
.welcome h1 span{color:var(--pink-deep)}
.welcome p{margin-top:14px;font-size:14px;line-height:20px;color:#8a99a4;width:230px}
.feature{top:470px;width:240px;height:254px;border:1px solid rgba(255,255,255,.6);padding:16px 15px}
.feature h2{font-size:19px;color:var(--white);text-align:center;letter-spacing:.5px;line-height:24px}
.feature .photo{margin-top:13px;width:207px;height:99px}
.feature p{margin-top:16px;font-size:9.6px;font-weight:700;line-height:14.5px;color:var(--white)}
.f-learn{left:136px;background:var(--sky)}
.f-create{left:392px;background:var(--lime)}
.f-share{left:649px;background:var(--pink)}
.intro-photo{left:138px;top:770px;width:111px;height:167px;background:linear-gradient(160deg,#7d5a45,#d9b4a0 55%,#efe0d6)}
.intro{left:264px;top:770px;width:360px}
.intro h2{font-size:16px;color:var(--blue)}
.intro p{margin-top:12px;font-size:9.4px;line-height:14.5px}
.intro p b{color:#6a7680}
.more{display:inline-block;margin-top:20px;font-size:8px;font-weight:700;color:var(--blue);border-bottom:1px solid var(--blue)}
.news{left:649px;top:768px;width:245px}
.news h2{font-size:15px;color:var(--blue)}
.news-item{display:flex;gap:17px;margin-top:14px}
.news-item + .news-item{margin-top:16px}
.date{width:47px;height:47px;flex:none;background:var(--pink);color:var(--white);text-align:center;padding-top:7px}
.date b{display:block;font-size:17px;font-weight:400;line-height:18px}
.date small{font-size:7px}
.news-item p{font-size:12.5px;line-height:20px;color:#7b8a95}
.news-item .link{font-size:7.5px;font-weight:700;color:var(--blue)}
.footer{left:0;top:998px;width:1024px;height:168px;background:var(--cream);border-top:1px solid #ececec}
.footer-brand{left:136px;top:1056px;font-size:22px}
.fcol{top:1030px;font-size:10px}
.fcol h3{font-size:11px;font-weight:600;color:var(--blue);margin-bottom:14px}
.fcol li{list-style:none;line-height:19px;letter-spacing:.5px;color:#8a8f92}
.fcol li::before{content:"›";color:#c8c8c8;margin-right:8px}
.fcol li.on{color:var(--green)}
.fcontact div{display:flex;align-items:flex-start;gap:10px;margin-bottom:10px;color:#7f868a;line-height:19px}
.fcontact div svg{margin-top:4px;flex:none}
.map{left:762px;top:1052px;width:126px;height:82px;background:linear-gradient(135deg,#e4e4e0,#d6dbe0 60%,#c9d4de)}
.bottom{left:0;top:1166px;width:1024px;height:34px;background:var(--lime);color:var(--white);font-size:9.5px;display:flex;align-items:center;justify-content:space-between;padding:0 160px 0 136px}
</style>
</head>
<body>

<div class="abs hero" role="img" aria-label="Photo of a smiling toddler playing with clay at a table"></div>

<header>
  <div class="abs brand header-brand">Puddle Jump</div>
  <div class="abs contact-bar">
    <div class="item">
      <svg width="16" height="16" viewBox="0 0 16 16"><circle cx="8" cy="9" r="5.5" fill="none" stroke="#add136" stroke-width="1.8"/><path d="M8 6v3.3l2 1.3" stroke="#add136" stroke-width="1.5" fill="none"/><path d="M2 4l2.5-2M14 4l-2.5-2" stroke="#add136" stroke-width="1.6"/></svg>
      (Mon - Fri) 8:00AM to 6:00PM
    </div>
    <div class="item">
      <svg width="24" height="14" viewBox="0 0 24 14"><path d="M0 3h4M1 7h3M0 11h4" stroke="#add136" stroke-width="1.2"/><rect x="6" y="1.5" width="16" height="11" fill="none" stroke="#add136" stroke-width="1.4"/><path d="M6 1.5l8 6 8-6" fill="none" stroke="#add136" stroke-width="1.4"/></svg>
      hello@puddlejumpkids.com
    </div>
    <div class="item">
      <svg width="15" height="15" viewBox="0 0 16 16"><path d="M3 1.5l2.5 2.8-1.3 1.8c.9 2 2.6 3.7 4.6 4.6l1.8-1.3 2.8 2.5-1.6 2.3C7.5 14 2 8.5 1.2 3z" fill="#add136"/><path d="M9.5 2.5a4 4 0 0 1 4 4M9.5 0.5a6 6 0 0 1 6 6" fill="none" stroke="#add136" stroke-width="1.1"/></svg>
      +(555) 240-7713
    </div>
  </div>
  <nav class="abs nav">
    <a class="active" href="#">Home</a>
    <a href="#">About</a>
    <a href="#">Services</a>
    <a href="#">Hours and Fees</a>
    <a href="#">Policies</a>
    <a href="#">Photos</a>
    <a href="#">Testimonials</a>
    <a href="#">Contact Us</a>
  </nav>
</header>

<section class="abs welcome">
  <h1 class="script">Welcome to<br><span>Puddle Jump Kidscare</span></h1>
  <p>a playspace where children can play, create, and imagine!</p>
</section>

<section class="abs feature f-learn">
  <h2 class="script">LEARNING</h2>
  <div class="photo" role="img" aria-label="Photo of children playing with building toys" style="background:linear-gradient(120deg,#d94b3a,#e9c27e 45%,#7cb3d8)"></div>
  <p>We develop age-appropriate activities that introduce and strengthen academic and social skills.</p>
</section>
<section class="abs feature f-create">
  <h2 class="script">CREATIVITY</h2>
  <div class="photo" role="img" aria-label="Photo of a child with paint-covered hands" style="background:linear-gradient(120deg,#3f5a2a,#d2a7b7 45%,#6a3f9e)"></div>
  <p>We offer children a wide range of creative opportunities including art projects, toddler yoga lessons, afternoon tea parties, dress up play, and a large selection of books and games.</p>
</section>
<section class="abs feature f-share">
  <h2 class="script">SHARING</h2>
  <div class="photo" role="img" aria-label="Photo of a child and an adult at a pretend tea party" style="background:linear-gradient(120deg,#c69a7a,#e7b9bb 45%,#8b4a3a)"></div>
  <p>We strive to include enrichment activities that extend your child's understanding of the world and their role in it.</p>
</section>

<div class="abs intro-photo" role="img" aria-label="Photo of the caregiver with a young child"></div>
<section class="abs intro">
  <h2 class="script">Welcome to Puddle Jump Kidscare!</h2>
  <p>We are a <b>licensed Group Family Day Care</b>, located in Brookfield's leafy Maple Hill. We are located on a pretty, tree-lined block on Linden Street, between Oak and Cedar Avenues. We are a few blocks from the green line tram and the Linden bus route, and we offer flexible hourly childcare, making it as easy as possible for busy parents on the go to arrange their children's care.</p>
  <p>We invite you to learn more about us and hope you will visit us soon</p>
  <a class="more">READ MORE</a>
</section>

<section class="abs news">
  <h2 class="script">Latest News</h2>
  <div class="news-item">
    <div class="date"><b>05</b><small>May 2014</small></div>
    <p>We are thrilled to have found a new cheerful space with a private backyard... <span class="link">▸READ MORE</span></p>
  </div>
  <div class="news-item">
    <div class="date"><b>05</b><small>May 2014</small></div>
    <p>We are thrilled to have found a new cheerful space with a private backyard... <span class="link">▸READ MORE</span></p>
  </div>
</section>

<footer>
  <div class="abs footer"></div>
  <div class="abs brand footer-brand">Puddle Jump</div>
  <div class="abs fcol" style="left:314px">
    <h3>Navigation</h3>
    <ul><li class="on">Home</li><li>About</li><li>Services</li><li>Contact</li></ul>
  </div>
  <div class="abs fcol" style="left:440px">
    <h3>Links</h3>
    <ul><li>Menu1</li><li>Menu1</li><li>Menu1</li><li>Menu1</li></ul>
  </div>
  <div class="abs fcol fcontact" style="left:568px">
    <h3>Contact Us</h3>
    <div><svg width="10" height="10" viewBox="0 0 16 16"><path d="M3 1.5l2.5 2.8-1.3 1.8c.9 2 2.6 3.7 4.6 4.6l1.8-1.3 2.8 2.5-1.6 2.3C7.5 14 2 8.5 1.2 3z" fill="#c3c6c8"/></svg>+1800-123-4567</div>
    <div><svg width="10" height="8" viewBox="0 0 10 8"><rect width="10" height="8" fill="#c3c6c8"/><path d="M0 0l5 4 5-4" stroke="#fff" fill="none"/></svg>info@yourwebsite.com</div>
    <div><svg width="9" height="12" viewBox="0 0 9 12"><path d="M4.5 0a4.5 4.5 0 0 1 4.5 4.5C9 8 4.5 12 4.5 12S0 8 0 4.5A4.5 4.5 0 0 1 4.5 0z" fill="#c3c6c8"/><circle cx="4.5" cy="4.5" r="1.6" fill="#fff"/></svg>Address, Your Country<br>Your Zip Code</div>
  </div>
  <div class="abs fcol" style="left:762px"><h3>Visit Us</h3></div>
  <div class="abs map" role="img" aria-label="Small street map showing the location"></div>
  <div class="abs bottom">
    <span>Copyright 2014 © CompanyName - All Rights Reserved</span>
    <span>Site Map &nbsp; • &nbsp; Privacy Policy</span>
  </div>
</footer>

</body>
</html>
```